Lawn sign for construction company

Would like this to be a very clean and high end design for luxury homes. We need a yard sign designed that includes the company logo, website, phone number and major service offerings (residential and commercial renovations and maintenance)
The company website is brackwellbuilders.com all other contact info is in the attachments
Target Market(s)
Luxury home owners and business owners
Industry/Entity Type
Construction/Home Improvement
Font styles to use
Other font styles liked:
- See company logo and other graphics included for title text fonts. All other fonts can be standard sans serif.
Colors
0054AA
0677BA
7BADD7
CADEEF
E8F1F8
Requirements
Must have
- Clean, easy to read design, would like 2 sided sign. A main sign side and back side which states “free estimates, and includes the website and phone number. Must also match the color scheme of the provided logo and other company images. Dark Navy blue primary color, gray secondary color, and orange as an accent color.
Nice to have
- 2nd sign side very simple design
Should not have
- Too many graphics limit to 1-3 colors

```html
<!DOCTYPE html>
<html lang="en">
<head>
<meta charset="utf-8">
<title>Brackwell Builders – Lawn Sign</title>
<link href="https://fonts.googleapis.com/css2?family=Montserrat:wght@400;500;600;800&display=swap" rel="stylesheet">
<style>
  :root {
    --navy: #020263;
    --orange: #ee7a12;
    --gray: #6b6b6b;
    --white: #ffffff;
    --stage: #8c8c8c;
  }
  * { margin: 0; padding: 0; box-sizing: border-box; }
  html, body { width: 1200px; height: 2355px; overflow: hidden; }
  body {
    background: var(--stage);
    font-family: "Montserrat", sans-serif;
    position: relative;
  }
  .sign {
    position: absolute;
    left: 100px;
    width: 1000px;
    height: 800px;
    overflow: hidden;
    box-shadow: 0 18px 30px rgba(0,0,0,0.35);
  }
  .sign--front { top: 250px; background: var(--white); }
  .sign--back { top: 1300px; background: var(--navy); }
  .sign svg { position: absolute; inset: 0; }

  .brand {
    position: absolute;
    top: 255px;
    left: 90px; right: 90px;
    display: flex;
    align-items: center;
    justify-content: center;
    gap: 22px;
    white-space: nowrap;
  }
  .brand__dot {
    flex: 0 0 auto;
    width: 56px; height: 56px;
    border-radius: 50%;
    background: var(--gray);
  }
  .brand__name {
    font-weight: 800;
    font-size: 52px;
    letter-spacing: 1px;
    color: var(--orange);
    text-transform: uppercase;
  }
  .services {
    position: absolute;
    top: 620px;
    left: 0; right: 0;
    text-align: center;
    color: var(--white);
    font-size: 43px;
    line-height: 64px;
    text-transform: uppercase;
    font-weight: 800;
  }
  .services .joiner { font-weight: 500; }

  .back__label {
    position: absolute;
    top: 125px; left: 0; right: 0;
    text-align: center;
    color: var(--white);
    font-weight: 800;
    font-size: 32px;
    letter-spacing: 6px;
  }
  .back__web {
    position: absolute;
    top: 540px; left: 0; right: 0;
    text-align: center;
    color: var(--white);
    font-weight: 600;
    font-size: 46px;
    letter-spacing: 1px;
  }
  .back__address {
    position: absolute;
    top: 630px; left: 0; right: 0;
    text-align: center;
    color: var(--white);
    font-weight: 500;
    font-size: 27px;
    line-height: 44px;
  }
</style>
</head>
<body>

  <section class="sign sign--front" aria-label="Front of sign">
    <svg width="1000" height="800" viewBox="0 0 1000 800">
      <rect x="32" y="32" width="936" height="736" fill="none" stroke="var(--navy)" stroke-width="5"/>
      <rect x="48" y="48" width="904" height="704" fill="none" stroke="var(--navy)" stroke-width="2"/>
      <path d="M0 430 Q500 740 1000 430 L1000 800 L0 800 Z" fill="var(--navy)"/>
    </svg>
    <div class="brand">
      <span class="brand__dot"></span>
      <span class="brand__name">Brackwell Builders</span>
    </div>
    <p class="services">
      Residential <span class="joiner">and</span> Commercial<br>
      Renovations <span class="joiner">and</span> Maintenance
    </p>
  </section>

  <section class="sign sign--back" aria-label="Back of sign">
    <svg width="1000" height="800" viewBox="0 0 1000 800">
      <rect x="32" y="32" width="936" height="736" fill="none" stroke="var(--white)" stroke-width="4"/>
      <rect x="48" y="48" width="904" height="704" fill="none" stroke="var(--white)" stroke-width="2"/>
      <polygon points="125,238 882,181 882,287 125,347" fill="var(--white)"/>
      <polygon points="125,389 882,328 882,437 125,500" fill="var(--white)"/>
      <text x="155" y="318" transform="rotate(-4.3 155 318)" textLength="690" lengthAdjust="spacingAndGlyphs"
            font-family="Montserrat, sans-serif" font-weight="800" font-size="78" fill="var(--orange)">FREE ESTIMATES</text>
      <text x="155" y="478" transform="rotate(-4.5 155 478)" textLength="695" lengthAdjust="spacingAndGlyphs"
            font-family="Montserrat, sans-serif" font-weight="800" font-size="104" fill="var(--orange)">555-271-0486</text>
    </svg>
    <p class="back__label">LICENSED AND INSURED</p>
    <p class="back__web">www.brackwellbuilders.com</p>
    <p class="back__address">Harlow Road<br>Maple Township, Michigan, MI, US 48000</p>
  </section>

</body>
</html>
```